Non fiction leadership Book Cover design needed for “Stay Bold: Build On Lasting Discipline”

I need a front cover design for a new book 6 X 9 traditional non-fiction book.

Title: "Stay BOLD - Build On Lasting Discipline"

The subtitle is not finalized- so use 2 lines of smaller dummy text

My brand guide is attached (please use the tan color sparingly)

I'd like to see BOLD look like it is in motion and "flying" across the page

Need CREATIVE designs and options

Do not want my picture on the front cover - I do want it on the back cover.

On the front cover I’d like to see creative use of font to create movement on “BOLD”

Target Market(s)

Business leaders

Industry/Entity Type

Aviation

Font styles to use
Other font styles liked:
• See style guide- can add additional font (modern script or san serif)

Colors
0054AA
0677BA
7BADD7
CADEEF
E8F1F8
EB3D1F
EC4F4E
F09395
F8D3D4
FCEDEE

Requirements
Must have
• Creative font use, using perspective to create movement/motion on BOLD
Should not have
• My picture on the front cover- my picture should be on the back cover

```html
<!DOCTYPE html>
<html lang="en">
<head>
<meta charset="utf-8">
<title>Stay Bold: Build On Lasting Discipline — Book Cover</title>
<link href="https://fonts.googleapis.com/css2?family=Bebas+Neue&family=Montserrat:wght@500;600&display=swap" rel="stylesheet">
<style>
  :root {
    --backdrop: #58595b;
    --brand-deep: #0054aa;
    --brand-mid: #0677ba;
    --brand-sky: #7badd7;
    --brand-mist: #cadeef;
    --cream: #faf1eb;
    --red: #eb3d1f;
    --gold: #d9a24a;
  }
  html, body {
    margin: 0;
    padding: 0;
    width: 1200px;
    height: 1200px;
    overflow: hidden;
    background: var(--backdrop);
  }
  .cover {
    position: absolute;
    left: 230px;
    top: 44px;
    width: 741px;
    height: 1111px;
    background: var(--cream);
    overflow: hidden;
  }
  .sky-art {
    position: absolute;
    inset: 0;
    width: 741px;
    height: 1111px;
  }
  .teaser {
    position: absolute;
    top: 44px;
    left: 0;
    width: 100%;
    margin: 0;
    text-align: center;
    color: var(--cream);
    font-family: "Montserrat", sans-serif;
    font-weight: 500;
    font-size: 15.6px;
    line-height: 19px;
  }
  .title-lead {
    position: absolute;
    top: 384px;
    left: 0;
    width: 100%;
    margin: 0;
    text-align: center;
    color: var(--red);
    font-family: "Bebas Neue", sans-serif;
    font-weight: 400;
    font-size: 138px;
    line-height: 138px;
    letter-spacing: -1px;
  }
  .motion-trails {
    position: absolute;
    left: 0;
    top: 540px;
    width: 741px;
    height: 420px;
  }
  .title-main {
    position: absolute;
    left: 150px;
    top: 552px;
    width: 461px;
    height: 399px;
    transform-origin: 50% 60%;
    transform: perspective(760px) rotateY(-24deg) skewX(-9deg);
  }
  .subtitle-bar {
    position: absolute;
    left: 140px;
    top: 960px;
    width: 461px;
    height: 49px;
    margin: 0;
    background: var(--brand-deep);
    color: var(--cream);
    font-family: "Montserrat", sans-serif;
    font-weight: 600;
    font-size: 22px;
    line-height: 49px;
    text-align: center;
    letter-spacing: 0.3px;
  }
  .author {
    position: absolute;
    top: 1024px;
    left: 0;
    width: 100%;
    margin: 0;
    text-align: center;
    color: var(--brand-deep);
    font-family: "Montserrat", sans-serif;
    font-weight: 600;
    font-size: 39px;
    line-height: 50px;
  }
</style>
</head>
<body>
  <main class="cover">
    <svg class="sky-art" viewBox="0 0 900 1350" preserveAspectRatio="none">
      <defs>
        <linearGradient id="sky-fill" x1="0" y1="0" x2="0" y2="1">
          <stop offset="0" stop-color="var(--brand-deep)"/>
          <stop offset="1" stop-color="var(--brand-mid)"/>
        </linearGradient>
      </defs>
      <path class="sky-band" fill="url(#sky-fill)"
        d="M0 0 H900 V447 A276 276 0 0 1 450 337 A276 276 0 0 1 0 447 Z"/>
      <rect class="aircraft-art" x="395" y="132" width="110" height="205" rx="18"
        fill="var(--brand-mist)" role="img"
        aria-label="White silhouette of a helicopter seen from above, rising into the sky"/>
    </svg>

    <p class="teaser">Lorem ipsum dolor sit amet, consectetuer adipiscing<br>sed diam nonummy nibh euismod tincidunt</p>
    <h1 class="title-lead">STAY</h1>

    <svg class="motion-trails" viewBox="0 0 741 420" aria-hidden="true">
      <g stroke-linecap="round">
        <line x1="24" y1="70" x2="170" y2="70" stroke="var(--brand-sky)" stroke-width="6"/>
        <line x1="60" y1="118" x2="175" y2="118" stroke="var(--brand-mist)" stroke-width="4"/>
        <line x1="10" y1="190" x2="165" y2="190" stroke="var(--brand-mid)" stroke-width="8"/>
        <line x1="70" y1="250" x2="168" y2="250" stroke="var(--red)" stroke-width="4"/>
        <line x1="30" y1="318" x2="172" y2="318" stroke="var(--brand-sky)" stroke-width="6"/>
        <line x1="90" y1="370" x2="178" y2="370" stroke="var(--brand-mist)" stroke-width="4"/>
      </g>
    </svg>

    <svg class="title-main" viewBox="0 0 560 490" preserveAspectRatio="none" role="img" aria-label="BOLD">
      <defs>
        <linearGradient id="word-fill" x1="0" y1="0" x2="1" y2="1">
          <stop offset="0" stop-color="var(--brand-sky)"/>
          <stop offset="0.35" stop-color="var(--brand-mid)"/>
          <stop offset="1" stop-color="var(--brand-deep)"/>
        </linearGradient>
        <radialGradient id="word-glow" cx="0.55" cy="0.95" r="0.5">
          <stop offset="0" stop-color="var(--gold)" stop-opacity="0.55"/>
          <stop offset="1" stop-color="var(--gold)" stop-opacity="0"/>
        </radialGradient>
      </defs>
      <text x="0" y="485" font-family="Bebas Neue, sans-serif" font-size="693"
        textLength="560" lengthAdjust="spacingAndGlyphs"
        fill="url(#word-fill)" stroke="var(--brand-deep)" stroke-width="4">BOLD</text>
      <text x="0" y="485" font-family="Bebas Neue, sans-serif" font-size="693"
        textLength="560" lengthAdjust="spacingAndGlyphs"
        fill="url(#word-glow)">BOLD</text>
    </svg>

    <p class="subtitle-bar">BUILD ON LASTING DISCIPLINE</p>
    <p class="author">Renata Halloway</p>
  </main>
</body>
</html>
```